Vernac Law Business cards and stationary design project

We are looking for a stationary design for business cards (double sided), 8x10, 5x7, and legal and standard envelopes.

We would like the design to match the logo that we have already.
Color palate preferred is Teal, White, grey and any others that will look good for a professional law firm.

We would like this statement: "RELATIONSHIPS. RESPECT. RESULT" to be on the back of the business cards and maybe on the stationary if it looks good.

Please see link to website for more information: www.vernac-law.example

Target Market(s)

Potential clients that need Attorney services.

Industry/Entity Type

Law Firm

Contact Information for Business Card

We would like the front and back to be two different colors. Current business cards are teal front, grey back and are a vertical design. We are open to options with colors.

Font styles to use
Serif

Colors
33a6d7
33b8a4
b9b9b9
5c5c5c

Requirements
Must have
• Logo supplied needs to go on the card and stationary.
• Match website color palate, www.vernac-law.example
• Be professional and not too wordy.
• Criminal Law, Civil Litigation, Personal Injury, Restraining Orders need to be on the card.
Nice to have
• RELATIONSHIPS. RESPECT. RESULTS. on the back of the card.
Should not have
• Not be too busy/wordy or too flashy.

```html
<!DOCTYPE html>
<html lang="en">
<head>
<meta charset="utf-8">
<title>Vernac Law Business Cards</title>
<link rel="stylesheet" href="https://fonts.googleapis.com/css2?family=Libre+Baskerville:wght@400;700&display=swap">
<style>
  :root {
    --stage: #2b2b2b;
    --card-grey: #5c5c5c;
    --card-white: #ffffff;
    --teal: #2a98a6;
    --ink-grey: #5c5c5c;
    --soft-white: #f2f2f2;
  }
  * { box-sizing: border-box; margin: 0; padding: 0; }
  html, body {
    width: 1200px;
    height: 900px;
    overflow: hidden;
    background: var(--stage);
    font-family: "Libre Baskerville", Georgia, serif;
  }
  .canvas {
    position: relative;
    width: 1200px;
    height: 900px;
  }
  .card {
    position: absolute;
    width: 560px;
    height: 320px;
    box-shadow: 0 10px 30px rgba(0, 0, 0, 0.45);
  }

  /* Back of card */
  .card-back {
    left: 150px;
    top: 90px;
    background: var(--card-grey);
    color: var(--soft-white);
  }
  .back-name {
    position: absolute;
    right: 40px;
    top: 70px;
    font-size: 42px;
    font-weight: 400;
    color: var(--card-white);
    letter-spacing: 1px;
    white-space: nowrap;
  }
  .back-footer {
    position: absolute;
    left: 36px;
    bottom: 28px;
    font-size: 13px;
    line-height: 1.5;
    letter-spacing: 0.5px;
  }
  .tagline { text-transform: uppercase; letter-spacing: 1px; }

  /* Front of card */
  .card-front {
    left: 500px;
    top: 480px;
    background: var(--card-white);
  }
  .front-brand {
    position: absolute;
    left: 36px;
    top: 132px;
    width: 230px;
    display: flex;
    align-items: center;
    gap: 10px;
    font-size: 22px;
    font-weight: 400;
    color: var(--teal);
    letter-spacing: 1.5px;
    text-transform: uppercase;
    white-space: nowrap;
  }
  .brand-dot {
    width: 12px;
    height: 12px;
    border-radius: 50%;
    background: var(--teal);
    flex: none;
  }
  .contact {
    position: absolute;
    left: 300px;
    top: 76px;
    width: 240px;
    color: var(--teal);
    font-size: 12.5px;
    line-height: 1.45;
  }
  .contact-name {
    font-size: 17px;
    font-weight: 700;
    text-transform: uppercase;
    letter-spacing: 0.5px;
  }
  .contact-role {
    color: var(--ink-grey);
    font-size: 13px;
    margin-bottom: 10px;
  }
  .contact-address { margin-bottom: 6px; }
  .contact-line {
    display: flex;
    align-items: center;
    gap: 8px;
    white-space: nowrap;
  }
  .contact-line svg {
    width: 11px;
    height: 11px;
    flex: none;
  }
</style>
</head>
<body>
  <main class="canvas">
    <section class="card card-back">
      <div class="back-name">Vernac Law</div>
      <div class="back-footer">
        <div class="website">www.vernac-law.example</div>
        <div class="tagline">Relationships. Respect. Result</div>
      </div>
    </section>

    <section class="card card-front">
      <div class="front-brand"><span class="brand-dot"></span>Vernac Law</div>

      <div class="contact">
        <div class="contact-name">Claire Doucet</div>
        <div class="contact-role">Lawyer</div>
        <div class="contact-address">418 Harbor View Ave.<br>#210 Seabrook, CA 90000</div>
        <div class="contact-line">
          <svg viewBox="0 0 12 12" aria-hidden="true"><path d="M2.5 1 L4.5 1 L5.3 3.4 L4 4.4 Q5 6.8 7.6 8 L8.6 6.7 L11 7.5 L11 9.5 Q10.5 11 9 11 Q1 10 1 2.5 Q1 1 2.5 1Z" fill="#5c5c5c"/></svg>
          <span>(555) 014-2736</span>
        </div>
        <div class="contact-line">
          <svg viewBox="0 0 12 12" aria-hidden="true"><rect x="1" y="2.5" width="10" height="7" fill="none" stroke="#5c5c5c" stroke-width="1.2"/><path d="M1 2.5 L6 6.5 L11 2.5" fill="none" stroke="#5c5c5c" stroke-width="1.2"/></svg>
          <span>claire@vernac-law.example</span>
        </div>
        <div class="contact-line">
          <svg viewBox="0 0 12 12" aria-hidden="true"><circle cx="6" cy="6" r="5" fill="none" stroke="#5c5c5c" stroke-width="1.1"/><ellipse cx="6" cy="6" rx="2.2" ry="5" fill="none" stroke="#5c5c5c" stroke-width="1"/><path d="M1 6 H11" stroke="#5c5c5c" stroke-width="1"/></svg>
          <span>www.vernac-law.example</span>
        </div>
      </div>
    </section>
  </main>
</body>
</html>
```